ORLA - Óptica Médica - web design and concept

Website concept - Create and develop our website design and structure. ORLA is an optical store chain, and we are looking to establish our web and digital concept. In attachment there are several pictures about our stores and our logo.

The website structure should be user friendly. Colors should be light and the design as simple and minimalist as possible. There are different variations of the logothat can be used, check the file.

The website will include optical collections and sun collections as an online store. Also, a medical menu should be considered in order for clients to schedule optometry appointments. There should also be a menu for client assistance where the clients can read about glass maintenance in our workshop.
Updates

Low design quality

Number of Pages Required

5+ page

Font styles to use
Serif
Sans Serif

Requirements
Must have
• Must be user-friendly and minimalist.
• Please USE PICTURES FROM THE BRANDS we sell: MERUN, BOSKA, PNW, KOLE, BAMPE
Nice to have
• Nice to inspire: ZEK glasses (see website https://ch.shopzek.com/en/)
• Nice to inspire: https://merun-eyewear.com/
• Nice to ispire: https://www.pnwglobe.com/en/
Should not have
• Hysteric colors and shapes

```html
<!DOCTYPE html>
<html lang="en">
<head>
<meta charset="utf-8">
<title>ORLA Óptica Médica</title>
<link href="https://fonts.googleapis.com/css2?family=Poppins:wght@400;500;600;700&display=swap" rel="stylesheet">
<style>
:root{
  --gold:#c8963e;
  --black:#111111;
  --ink:#222222;
  --grey-bg:#eeeeee;
  --slate:#c9ccd6;
  --white:#ffffff;
}
*{margin:0;padding:0;box-sizing:border-box}
html,body{width:1200px;height:3805px;overflow:hidden}
body{font-family:'Poppins',sans-serif;color:var(--ink);background:var(--white);position:relative}
.section{position:absolute;left:0;width:1200px}
.abs{position:absolute}
.gold-title{color:var(--gold);font-weight:700;font-size:31px;text-align:center;width:1200px;left:0}
/* header */
.site-header{top:0;height:106px;background:var(--black)}
.brand{left:132px;top:30px;color:var(--gold);font-weight:600;font-size:34px;letter-spacing:4px;display:flex;align-items:center;gap:12px}
.brand .mark{width:26px;height:26px;border:2px solid var(--gold)}
.brand small{position:absolute;left:40px;top:44px;font-size:8px;letter-spacing:3px;font-weight:500}
.nav a{position:absolute;top:44px;color:var(--white);font-size:13px;font-weight:500;text-decoration:none;white-space:nowrap}
/* hero */
.hero{top:106px;height:617px;background:linear-gradient(120deg,#8a6a35 0%,#3a3430 55%,#2c5a5a 80%,#e8d6a8 100%)}
.hero h1{left:132px;top:186px;color:var(--black);font-size:40px;font-weight:700}
.hero p{left:132px;top:244px;width:440px;font-size:15px;font-weight:600;color:var(--black);line-height:1.45}
.btn-white{background:var(--white);color:var(--black);font-weight:600;font-size:13px;border-radius:30px;padding:14px 20px;white-space:nowrap}
.hero .btn-white{left:132px;top:314px}
.dots{left:132px;top:528px;display:flex;gap:12px;align-items:center}
.dots span{width:8px;height:8px;border-radius:50%;background:var(--black)}
.dots span.on{width:16px;height:16px;border:2px solid var(--black);background:transparent;position:relative}
.dots span.on::after{content:"";position:absolute;left:3px;top:3px;width:6px;height:6px;border-radius:50%;background:var(--black)}
/* services */
.services{top:723px;height:571px}
.services .gold-title{top:82px}
.intro{left:222px;width:756px;top:142px;font-size:13px;line-height:1.75;text-align:center;color:var(--ink)}
.service{width:280px;text-align:center}
.service svg{display:block;margin:0 auto}
.service h3{margin-top:22px;color:var(--gold);font-size:17px;font-weight:500}
.service p{margin:14px auto 0;width:250px;font-size:13px;line-height:1.7}
.service a{display:inline-block;margin-top:24px;color:var(--gold);font-size:13px;text-decoration:underline;font-weight:500}
.arrow{width:22px;height:22px;border:1.5px solid var(--ink);border-radius:50%;top:339px}
/* about */
.about{top:1294px;height:401px;background:var(--slate)}
.about-photo{left:440px;top:0;width:760px;height:401px;background:linear-gradient(90deg,var(--slate) 0%,#b7a99c 30%,#9c8a7c 60%,#c8c4c0 100%)}
.about h2{left:132px;top:80px;color:var(--gold);font-size:30px;font-weight:700}
.about p{left:132px;top:140px;width:280px;font-size:12.5px;line-height:1.75;color:var(--ink)}
.btn-gold{background:var(--gold);color:var(--white);font-size:12px;font-weight:600;border-radius:30px;padding:14px 22px;white-space:nowrap}
.about .btn-gold{left:132px;top:306px}
/* call */
.call{top:1695px;height:157px;background:var(--gold)}
.call h2{left:132px;top:22px;color:var(--white);font-size:30px;font-weight:700}
.call p{left:132px;top:76px;width:620px;color:var(--white);font-size:13px;font-weight:600;line-height:1.6}
.call .btn-white{left:827px;top:60px;width:145px;text-align:center;color:var(--gold);padding:12px 0}
/* channel */
.channel{top:1852px;height:647px}
.channel .gold-title{top:68px}
.channel .intro{top:126px;left:220px;width:760px}
.channel-card{left:188px;top:213px;width:824px;height:353px;background:#b5b5b5;box-shadow:0 6px 14px rgba(0,0,0,.3)}
.channel-art{left:142px;top:40px;width:177px;height:280px;background:linear-gradient(180deg,#9a9a9a,#7a7a7a)}
.channel-card p{left:355px;top:120px;width:380px;font-size:13px;line-height:1.75;color:var(--ink)}
.play{left:45px;top:283px}
/* blog */
.blog{top:2499px;height:723px;background:var(--grey-bg)}
.blog .gold-title{top:45px}
.photo-store{background:linear-gradient(160deg,#4a4a48 0%,#7a6a52 45%,#a87a48 70%,#3c6060 100%)}
.photo-store-alt{background:linear-gradient(180deg,#2a2a2a 0%,#b09060 40%,#3c6c6c 70%,#c8a070 100%)}
.meta{font-size:13px;color:var(--ink)}
.post-title{color:var(--gold);font-size:17px;font-weight:500}
.read{color:var(--gold);font-size:12px;font-weight:600}
.blog .excerpt{left:134px;top:538px;width:400px;font-size:12.5px;line-height:1.6}
.blog .btn-gold{left:134px;top:619px;padding:10px 22px;font-size:11px}
/* brands */
.brands{top:3222px;height:266px}
.brands .gold-title{top:36px}
.brand-tile{top:119px;width:158px;height:84px;background:var(--white);box-shadow:0 2px 8px rgba(0,0,0,.25);display:flex;align-items:center;justify-content:center;font-weight:600;font-size:17px;color:var(--black);letter-spacing:1px}
/* footer */
.site-footer{top:3488px;height:317px;background:var(--black);color:var(--white)}
.site-footer h4{position:absolute;top:40px;font-size:13px;font-weight:600}
.col{position:absolute;top:82px;font-size:12px;line-height:23px}
.contact-row{display:flex;gap:14px;align-items:flex-start;margin-bottom:14px;line-height:18px}
.news p{width:230px;line-height:20px}
.signup{position:absolute;left:830px;top:178px;width:223px;height:36px;display:flex}
.signup span{flex:1;background:var(--white);color:#999;font-size:10px;padding:11px 10px}
.signup b{width:36px;background:var(--gold);display:flex;align-items:center;justify-content:center}
.copy{position:absolute;left:0;top:277px;width:1200px;text-align:center;font-size:11px}
</style>
</head>
<body>

<header class="section site-header">
  <div class="abs brand"><span class="mark"></span>ORLA<small>ÓPTICA MÉDICA</small></div>
  <nav class="nav">
    <a style="left:380px">START</a>
    <a style="left:450px">COLLECTIONS ▾</a>
    <a style="left:578px">APPOINTMENTS</a>
    <a style="left:700px">ASSISTANCE</a>
    <a style="left:807px">BLOG</a>
    <a style="left:883px">STORE ▾</a>
    <svg class="abs" style="left:980px;top:43px" width="16" height="16" viewBox="0 0 16 16"><circle cx="6.5" cy="6.5" r="5" fill="none" stroke="#fff" stroke-width="2"/><path d="M10 10l5 5" stroke="#fff" stroke-width="2"/></svg>
    <svg class="abs" style="left:1020px;top:44px" width="18" height="15" viewBox="0 0 18 15"><path d="M0 1h3l2 9h10l2-7H4.5" fill="none" stroke="#fff" stroke-width="1.6"/><circle cx="7" cy="13" r="1.4" fill="#fff"/><circle cx="14" cy="13" r="1.4" fill="#fff"/></svg>
    <a style="left:1044px">(0)</a>
  </nav>
</header>

<section class="section hero" role="img" aria-label="Interior of a modern optical store with wooden displays and teal wall panels">
  <svg class="abs" style="left:0;top:0" width="1200" height="617" viewBox="0 0 1200 617"><polygon points="0,0 780,0 470,617 0,617" fill="#c89a48" opacity="0.93"/></svg>
  <h1 class="abs">The New Optical Store</h1>
  <p class="abs">We will be happy to help you and offer you the best solution for your visual health problems.</p>
  <span class="abs btn-white">BOOK YOUR APPOINTMENT</span>
  <div class="abs dots"><span class="on"></span><span></span><span></span></div>
</section>

<section class="section services">
  <h2 class="abs gold-title">What we do!</h2>
  <p class="abs intro">Lorem ipsum dolor sit amet, consectetuer adipiscing elit, sed diam nonummy nibh euismod tincidunt ut laoreet dolore magna aliquam erat volutpat. Ut wisi enim ad minim veniam</p>
  <svg class="abs arrow" style="left:90px" viewBox="0 0 22 22"><path d="M13 6l-5 5 5 5" fill="none" stroke="#222" stroke-width="1.6"/></svg>
  <svg class="abs arrow" style="left:1090px" viewBox="0 0 22 22"><path d="M9 6l5 5-5 5" fill="none" stroke="#222" stroke-width="1.6"/></svg>
  <div class="abs service" style="left:139px;top:230px">
    <svg width="48" height="48" viewBox="0 0 48 48"><circle cx="24" cy="24" r="21" fill="none" stroke="#c8963e" stroke-width="2.5"/><circle cx="17" cy="21" r="2" fill="#c8963e"/><circle cx="31" cy="21" r="2" fill="#c8963e"/><path d="M15 30q9 8 18 0" fill="none" stroke="#c8963e" stroke-width="2.5"/></svg>
    <h3>Orla Childhood Guarantee</h3>
    <p>50% discount on new glasses, if your child's graduation has changed before six months.</p>
    <a>Details</a>
  </div>
  <div class="abs service" style="left:444px;top:230px">
    <svg width="60" height="48" viewBox="0 0 60 48"><path d="M3 12h34v24H3zM37 20h12l8 8v8H37z" fill="none" stroke="#c8963e" stroke-width="2.5"/><path d="M20 17v14M13 24h14" stroke="#c8963e" stroke-width="3"/><circle cx="13" cy="38" r="4" fill="#fff" stroke="#c8963e" stroke-width="2.5"/><circle cx="47" cy="38" r="4" fill="#fff" stroke="#c8963e" stroke-width="2.5"/></svg>
    <h3>Orla Accident Warranty</h3>
    <p>Did you get off your glasses when you got out of the car? Did your little boy play with his sunglasses?</p>
    <a>Details</a>
  </div>
  <div class="abs service" style="left:776px;top:230px">
    <svg width="48" height="48" viewBox="0 0 48 48"><rect x="4" y="8" width="40" height="36" fill="none" stroke="#c8963e" stroke-width="2.5"/><path d="M4 17h40M14 3v9M34 3v9" stroke="#c8963e" stroke-width="2.5"/><g fill="#c8963e"><rect x="10" y="22" width="6" height="5"/><rect x="21" y="22" width="6" height="5"/><rect x="32" y="22" width="6" height="5"/><rect x="10" y="32" width="6" height="5"/><rect x="21" y="32" width="6" height="5"/><rect x="32" y="32" width="6" height="5"/></g></svg>
    <h3>Manufacturer's Warranty</h3>
    <p>All our products have the legal guarantee of the manufacturer. They will be free parts..</p>
    <a>Details</a>
  </div>
</section>

<section class="section about">
  <div class="abs about-photo" role="img" aria-label="Smiling customer trying on glasses in front of an eyewear display wall"></div>
  <h2 class="abs">Orla Optics</h2>
  <p class="abs">ORLA OPTICA opens its doors with a clear purpose: to take care of you. Our priority is your visual health, and for this reason we have the best professionals and the most competitive products to serve your needs.</p>
  <span class="abs btn-gold">GET TO KNOW AS BETTER</span>
</section>

<section class="section call">
  <h2 class="abs">Call Us</h2>
  <p class="abs">BOOK YOUR APPOINTMENT WITH US. We will be happy to help you and offer you the best solution for your visual health problems.</p>
  <span class="abs btn-white">CONTACT</span>
</section>

<section class="section channel">
  <h2 class="abs gold-title">Follow Us On Vidora</h2>
  <p class="abs intro">Welcome to Vidora's optics and optometry channel . We are here to advise, explain and guide you if you need any help related to the world of vision.</p>
  <div class="abs channel-card">
    <div class="abs channel-art" role="img" aria-label="Channel illustration of an optician with glasses and lettered channel title"></div>
    <p class="abs">In the channel we will have advice, UNBOXING news, explanations with criteria and many collaborations of experts in this sector so that nothing escapes us.</p>
    <svg class="abs play" width="38" height="38" viewBox="0 0 38 38"><circle cx="19" cy="19" r="16" fill="none" stroke="#c0392b" stroke-width="3"/><path d="M15 12l11 7-11 7z" fill="#c0392b"/></svg>
  </div>
</section>

<section class="section blog">
  <h2 class="abs gold-title">Latest Blog</h2>
  <div class="abs photo-store" style="left:134px;top:122px;width:437px;height:312px" role="img" aria-label="Optical store interior with a central wooden counter"></div>
  <span class="abs meta" style="left:134px;top:458px">Posted on 18 Jun 2018</span>
  <span class="abs post-title" style="left:134px;top:492px">But I must explain to you how</span>
  <p class="abs excerpt">Sed ut perspiciatis unde omnis iste natus error sit voluptatem accusantium doloremque laudantium, totam rem aperiam</p>
  <span class="abs btn-gold">READ MORE</span>

  <div class="abs photo-store-alt" style="left:611px;top:124px;width:457px;height:180px" role="img" aria-label="Optical store display wall with teal panels"></div>
  <span class="abs meta" style="left:611px;top:320px">Posted on 20 Jun 2018</span>
  <span class="abs post-title" style="left:611px;top:348px">But I must explain to you how</span>
  <span class="abs read" style="left:988px;top:352px">Read More</span>

  <div class="abs photo-store-alt" style="left:611px;top:388px;width:457px;height:180px" role="img" aria-label="Wide view of optical store shelves and seating"></div>
  <span class="abs meta" style="left:611px;top:584px">Posted on 20 Jun 2018</span>
  <span class="abs post-title" style="left:611px;top:612px">But I must explain to you how</span>
  <span class="abs read" style="left:988px;top:616px">Read More</span>
</section>

<section class="section brands">
  <h2 class="abs gold-title">Our brands</h2>
  <div class="abs brand-tile" style="left:152px">MERUN</div>
  <div class="abs brand-tile" style="left:330px">BOSKA</div>
  <div class="abs brand-tile" style="left:512px">PNW</div>
  <div class="abs brand-tile" style="left:698px">KOLE</div>
  <div class="abs brand-tile" style="left:880px">BAMPE</div>
</section>

<footer class="section site-footer">
  <h4 style="left:132px">LINKS</h4>
  <h4 style="left:302px">OUR GUARANTEES</h4>
  <h4 style="left:551px">CONTACT US</h4>
  <h4 style="left:830px">NEWSLETTER</h4>
  <div class="col" style="left:132px">Start<br>Collections<br>Appointments<br>Assistance<br>Blog<br>Store</div>
  <div class="col" style="left:302px">Orla Childhood Guarantee<br>Orla Accident Warranty<br>Orla Security<br>Orla Vision<br>Manufacturer's Warranty</div>
  <div class="col" style="left:551px">
    <div class="contact-row"><svg width="12" height="16" viewBox="0 0 12 16"><path d="M6 15S1 9 1 6a5 5 0 0110 0c0 3-5 9-5 9z" fill="none" stroke="#fff" stroke-width="1.4"/><circle cx="6" cy="6" r="1.8" fill="#fff"/></svg><span>Calle Olmos,<br>15. Valverde</span></div>
    <div class="contact-row"><svg width="14" height="14" viewBox="0 0 14 14"><path d="M3 1l3 3-2 2q2 3 4 4l2-2 3 3-2 2Q5 13 1 3z" fill="#fff"/></svg><span>+34 900 12 34 56</span></div>
    <div class="contact-row"><svg width="14" height="12" viewBox="0 0 14 12"><rect x="1" y="1" width="12" height="10" fill="none" stroke="#fff" stroke-width="1.3"/><path d="M1 1l6 5 6-5" fill="none" stroke="#fff" stroke-width="1.3"/></svg><span>orlaoptico@mailbox.es</span></div>
  </div>
  <div class="col news" style="left:830px"><p>But I must explain to you how all this mistaken idea of denouncing pleasure and praising.</p></div>
  <div class="signup"><span>Enter your email address</span><b><svg width="12" height="12" viewBox="0 0 12 12"><path d="M1 6h9M6 2l4 4-4 4" fill="none" stroke="#fff" stroke-width="1.6"/></svg></b></div>
  <p class="copy">© 2018 Orlaoptica | All Rights Reserved</p>
</footer>

</body>
</html>
```